Want a package created for a new protein bar

We would like a new package created for a new protein bar project The name of the bar will be VORNBar a real food protein bar, we would like a ‘window’ on the package of bar like Bold Meadow bar below in images.

VORNBar
‘Super Food Bar’
14g of Whey Protein
The package film size is the following 12cm width x 15cm Length,
Flavor Peanut Chocolate Chip, additional information will be attached shortly like nutrition facts,

Target Market(s)

fitness market, bodybuilders, athletes, everyday people

Industry/Entity Type

Health Product

Logo Text

VORNBar

Font styles to use
Serif
Sans Serif
Decorative

Requirements
Must have
• Package window

```html
<!DOCTYPE html>
<html lang="en">
<head>
<meta charset="utf-8">
<title>VORNBar – Peanut Chocolate Chip Wrapper</title>
<link href="https://fonts.googleapis.com/css2?family=Montserrat:wght@500;700;900&family=Poppins:ital,wght@1,800&display=swap" rel="stylesheet">
<style>
  :root{
    --backdrop:#5e1416;
    --crimson:#8a1a1c;
    --crimson-deep:#5a0f11;
    --ink:#161415;
    --graphite:#3a3a3c;
    --steel:#6c6c6e;
    --silver:#c9c9cb;
    --white:#ffffff;
    --gold:#c8913a;
    --oat:#b98c55;
    --oat-dark:#6b4424;
  }
  *{margin:0;padding:0;box-sizing:border-box}
  html,body{width:1200px;height:1200px;overflow:hidden;background:var(--backdrop)}
  .canvas{position:relative;width:1200px;height:1200px;background:var(--backdrop)}
  .wrapper{position:absolute;left:48px;top:380px;width:1104px;height:410px;overflow:hidden;
    background:linear-gradient(180deg,var(--crimson) 0,var(--crimson-deep) 46%,var(--silver) 46.3%,var(--silver) 48.3%,var(--steel) 48.6%,var(--graphite) 100%)}
  .crimp{position:absolute;top:0;width:82px;height:100%;
    background:linear-gradient(180deg,var(--crimson-deep) 0,#3a0b0c 55%,var(--ink) 55.5%,#222 100%)}
  .crimp--left{left:0}
  .crimp--right{right:0}
  .crimp::after{content:"";position:absolute;inset:0;
    background:repeating-linear-gradient(180deg,rgba(0,0,0,.28) 0 3px,transparent 3px 7px)}
  .base-left{position:absolute;left:82px;top:278px;width:390px;height:132px;
    background:linear-gradient(90deg,var(--ink),var(--graphite))}
  .window{position:absolute;left:82px;top:2px;width:333px;height:276px;
    background:radial-gradient(circle at 40% 40%,var(--oat) 0,#8c6338 55%,var(--oat-dark) 100%)}
  .accent-lines{position:absolute;left:0;top:0}
  .brand-banner{position:absolute;left:421px;top:61px;width:444px;height:112px;
    background:linear-gradient(90deg,var(--ink) 0,#242224 70%,rgba(36,34,36,0) 100%);
    border-radius:18px 0 0 0;display:flex;align-items:center;padding-left:34px;gap:18px}
  .brand-mark{width:26px;height:26px;background:var(--white);flex:none}
  .brand-name{font-family:"Montserrat",sans-serif;font-weight:900;font-size:84px;line-height:1;
    color:var(--white);letter-spacing:-1px;white-space:nowrap}
  .tagline{position:absolute;left:429px;top:222px;font-family:"Montserrat",sans-serif;font-weight:500;
    font-size:18.5px;letter-spacing:4.2px;color:var(--white);white-space:nowrap}
  .flavor{position:absolute;left:104px;top:305px;font-family:"Poppins",sans-serif;font-style:italic;
    font-weight:800;font-size:24px;color:var(--white);white-space:nowrap}
  .claims{position:absolute;left:666px;top:303px;display:flex;height:44px;border:2px solid var(--white);
    border-radius:12px 4px 12px 4px}
  .claim{display:flex;flex-direction:column;align-items:center;justify-content:center;width:84px;
    border-left:2px solid var(--white);font-family:"Poppins",sans-serif;font-style:italic;font-weight:800;
    color:var(--white);line-height:1}
  .claim:first-child{border-left:none}
  .claim__value{font-size:18px}
  .claim__value small{font-size:10px}
  .claim__label{font-size:9.5px;margin-top:2px;text-align:center}
  .tear-line{position:absolute;left:82px;right:82px;top:370px;border-top:1.5px dashed #d12a2a}
</style>
</head>
<body>
<main class="canvas">
  <section class="wrapper" aria-label="VORNBar wrapper, flat">
    <div class="window" role="img" aria-label="Package window showing the oat, peanut and chocolate chip bar with chocolate chip cookies"></div>
    <div class="base-left"></div>
    <svg class="accent-lines" width="1104" height="410" viewBox="0 0 1104 410" aria-hidden="true">
      <line x1="880" y1="40" x2="780" y2="220" stroke="var(--gold)" stroke-width="1.2"/>
      <line x1="960" y1="60" x2="880" y2="220" stroke="var(--gold)" stroke-width="1.2"/>
      <line x1="900" y1="30" x2="1022" y2="90" stroke="var(--gold)" stroke-width="1"/>
    </svg>
    <div class="brand-banner">
      <span class="brand-mark" aria-hidden="true"></span>
      <span class="brand-name">VORNBAR</span>
    </div>
    <p class="tagline">Snack with High Protein | Super food bar</p>
    <p class="flavor">Peanut Chocolate Chip</p>
    <div class="claims">
      <div class="claim"><span class="claim__value">14<small>g</small></span><span class="claim__label">WHEY<br>PROTEIN</span></div>
      <div class="claim"><span class="claim__value">120</span><span class="claim__label">CALORIES</span></div>
      <div class="claim"><span class="claim__value">5.25<small>g</small></span><span class="claim__label">PROTEIN</span></div>
      <div class="claim"><span class="claim__label">GLUTTEN<br>FREE</span></div>
    </div>
    <div class="tear-line"></div>
    <div class="crimp crimp--left"></div>
    <div class="crimp crimp--right"></div>
  </section>
</main>
</body>
</html>
```